Upscale business cards needed for Board of Directors

We need professional business cards created for members of our family business Board of Directors. We would like these relatively simple and straightforward, but also with a unique element to set them apart. Probably stick with neutral and simple colors - white, grey etc. We need space for the traditional elements, including name, title, address, email/phone number. And we will be creating several from this template so it needs to be template that is easy to switch information in and out of.
Business
See description

```html
<!DOCTYPE html>
<html lang="en">
<head>
<meta charset="utf-8">
<title>Harbourline Holdings – Business Card</title>
<link rel="stylesheet" href="https://fonts.googleapis.com/css2?family=Lato:wght@400;900&family=Marcellus+SC&family=Courier+Prime&display=swap">
<style>
  :root {
    --page-bg: #ece9e6;
    --card-white: #ffffff;
    --card-grey: #a39d9b;
    --name-box: #d9d5d3;
    --ink-dark: #1f1f22;
    --ink-mid: #6e6a69;
    --ink-light: #ffffff;
  }
  * { margin: 0; padding: 0; box-sizing: border-box; }
  html, body {
    width: 1200px; height: 799px; overflow: hidden;
    background: var(--page-bg);
  }
  .business-card {
    position: absolute; left: 150px; top: 142px;
    width: 900px; height: 514px;
    background: var(--card-grey);
    box-shadow: 0 12px 30px rgba(0,0,0,0.18);
    overflow: hidden;
  }
  .card-header {
    position: absolute; left: 0; top: 0; width: 100%; height: 236px;
    background: var(--card-white);
  }
  .company-name {
    position: absolute; left: 56px; top: 58px;
    font-family: "Lato", sans-serif; font-weight: 900;
    color: var(--ink-dark); line-height: 1;
  }
  .company-name .primary { display: block; font-size: 64px; letter-spacing: 1px; }
  .company-name .secondary { display: block; font-size: 30px; letter-spacing: 18px; margin: 12px 0 0 70px; }
  .name-plate {
    position: absolute; left: 572px; top: 192px;
    width: 292px; height: 108px;
    background: var(--name-box); border-radius: 14px;
    padding: 22px 24px;
  }
  .person-name {
    font-family: "Marcellus SC", serif; font-size: 30px;
    color: var(--ink-dark); white-space: nowrap;
  }
  .person-title {
    font-family: "Courier Prime", monospace; font-size: 20px;
    color: var(--ink-mid); letter-spacing: 2px; margin-top: 4px;
  }
  .contact-item {
    position: absolute; display: flex; align-items: flex-start; gap: 14px;
    font-family: "Lato", sans-serif; font-size: 21px; line-height: 1.3;
    color: var(--ink-light);
  }
  .contact-item svg { flex: none; width: 24px; height: 24px; margin-top: 2px; }
  .contact-address { left: 56px; top: 272px; }
  .contact-phone { left: 56px; top: 372px; }
  .contact-web { left: 450px; top: 336px; }
  .contact-email { left: 450px; top: 398px; }
</style>
</head>
<body>
  <article class="business-card">
    <header class="card-header">
      <h1 class="company-name">
        <span class="primary">HARBOURLINE</span>
        <span class="secondary">HOLDINGS</span>
      </h1>
    </header>

    <div class="name-plate">
      <p class="person-name">Name Surname</p>
      <p class="person-title">Designation</p>
    </div>

    <div class="contact-item contact-address">
      <svg viewBox="0 0 24 24" aria-hidden="true"><circle cx="12" cy="12" r="12" fill="#fff"/><path d="M12 5a4.5 4.5 0 0 0-4.5 4.5C7.5 13 12 18 12 18s4.5-5 4.5-8.5A4.5 4.5 0 0 0 12 5zm0 6.2a1.7 1.7 0 1 1 0-3.4 1.7 1.7 0 0 1 0 3.4z" fill="#a39d9b"/></svg>
      <p>118 W. Meadow Crest Ave.<br>Alder Bend, TX. 75510</p>
    </div>

    <div class="contact-item contact-phone">
      <svg viewBox="0 0 24 24" aria-hidden="true"><circle cx="12" cy="12" r="11" fill="none" stroke="#fff" stroke-width="2"/><path d="M8.6 6.5l1.8-.3 1 2.6-1.3 1a7 7 0 0 0 3.2 3.2l1-1.3 2.6 1-.3 1.8c-.1.6-.7 1-1.3.9A9 9 0 0 1 7.6 7.8c0-.6.4-1.2 1-1.3z" fill="#fff"/></svg>
      <p>(555) 210 - 4638</p>
    </div>

    <div class="contact-item contact-web">
      <svg viewBox="0 0 24 24" aria-hidden="true"><circle cx="12" cy="12" r="12" fill="#fff"/><circle cx="12" cy="12" r="6" fill="none" stroke="#a39d9b" stroke-width="1.6"/><path d="M6 12h12M12 6c-2.5 3.5-2.5 8.5 0 12M12 6c2.5 3.5 2.5 8.5 0 12" fill="none" stroke="#a39d9b" stroke-width="1.4"/></svg>
      <p>www.NorthwoodCapital.co</p>
    </div>

    <div class="contact-item contact-email">
      <svg viewBox="0 0 24 24" aria-hidden="true"><circle cx="12" cy="12" r="12" fill="#fff"/><rect x="6" y="8" width="12" height="8.5" rx="1" fill="none" stroke="#a39d9b" stroke-width="1.6"/><path d="M6.5 8.8L12 13l5.5-4.2" fill="none" stroke="#a39d9b" stroke-width="1.6"/></svg>
      <p>Maya@NorthwoodCapital.co</p>
    </div>
  </article>
</body>
</html>
```